Title: Iron Ledger Sub: She never leaves the harbor - Book cover

I need a complete book cover, front, spine, and back.

Religions Book

This book is more about the Title so it should be strong and serious.

Like the color Deep Red and black, blue. Deep purple
Avoid greens, orange, yellows.

Maybe a picture of a strong hand on the Bible. OR someone yelling.

If any pictures are used they must be 100% royalty free with proof or a buyout of image.

I have attached a couple of designs that the client likes. Just as a reference. The exception they DIDN'T like the pictures in the book cover.

Please ask any questions to clarify.

Please see the file I just uploaded called 'Book Cover samples.png" The clients likes the Title: Salt and Ember" the best. Please create a design something closer to this. The like how the title jumps off the page with a 2D look.

Again the Title must standout, and any use of images must be a secondary to the design.

I am happy with we the designs that have been submitted so far.

I hope this helps you get closer.

Thank you

First of all I want to thank you for all of your designs. At the beginning the client thought he would like a picture that represented the title. But after looking at all of the designs. He has now decided NOT to have any pictures.

Here is what he wants

1. BOLD Font (San Serif only) no fancy versions for the Title "IRON LEDGER" in uppercase. The title font should have some dimension to it to appear 2D or 3D looks. Shiny look. It needs to looks like it jumping off the page.

2. The subtitle right below the title in San Serif font)

3. Background solid color either black, dark red, or dark blue. The background can be slightly textured or gradation fill, etc.

4. The cover must have a strong and bold statement.

Thank you again.

Please use this photo on the back cover.

Thank you

Requirements
Should not have
• A picture that over powers the Title.

```html
<!DOCTYPE html>
<html lang="en">
<head>
<meta charset="utf-8">
<title>Iron Ledger – Book Cover</title>
<link href="https://fonts.googleapis.com/css2?family=Montserrat:wght@400;500;600;700&display=swap" rel="stylesheet">
<style>
  :root {
    --ink-black: #0b0b0b;
    --back-grey: #3a3a3a;
    --spine-edge: #8a8a8a;
    --white: #ffffff;
    --gold-dark: #8a6a35;
    --gold-light: #f1dfae;
    --deep-red: #b3121a;
    --title-red: #9e1a1d;
    --sky-blue: #4f87c4;
    --sky-light: #d3dfe8;
    --dusk-purple: #4a3a7a;
    --night-purple: #1e1438;
  }
  * { margin: 0; padding: 0; box-sizing: border-box; }
  html, body { width: 1200px; height: 847px; overflow: hidden; background: #fff; }
  .cover {
    position: relative; width: 1200px; height: 847px;
    font-family: "Montserrat", "Helvetica Neue", Arial, sans-serif;
    color: var(--white);
  }

  /* Shared title lockup */
  .title-block { position: absolute; text-align: center; font-weight: 600; }
  .title-main { display: block; line-height: 1; letter-spacing: 2px; }
  .title-rule {
    display: block; height: 5px; margin: 0 auto;
    background: linear-gradient(90deg, var(--gold-dark), var(--gold-light) 50%, var(--gold-dark));
  }
  .title-sub { display: block; line-height: 1; letter-spacing: 1px; }

  /* Back cover */
  .back {
    position: absolute; left: 0; top: 0; width: 543px; height: 847px;
    background: linear-gradient(90deg, var(--ink-black) 0%, #202020 55%, var(--back-grey) 100%);
  }
  .back .title-block { left: 40px; top: 56px; width: 460px; }
  .back .title-main { font-size: 96px; }
  .back .title-rule { width: 292px; margin-top: 10px; }
  .back .title-sub { font-size: 62px; margin-top: 8px; }

  .author-bio {
    position: absolute; left: 46px; top: 294px; width: 447px;
    font-size: 12.5px; line-height: 23.4px; text-align: justify;
    font-variant: small-caps; font-weight: 500;
  }
  .author-photo {
    float: left; width: 188px; height: 208px; margin: 4px 12px 4px 0;
    background: linear-gradient(160deg, #f2f2f2 0%, #d8c4b6 55%, #3d4e7a 100%);
  }
  .site-button {
    position: absolute; left: 46px; top: 742px; width: 447px; height: 44px;
    background: linear-gradient(180deg, #e2262c 0%, var(--deep-red) 60%, #8d0d12 100%);
    font-size: 24px; font-weight: 600; letter-spacing: 1px;
    display: flex; align-items: center; justify-content: center;
  }

  /* Spine */
  .spine {
    position: absolute; left: 543px; top: 0; width: 114px; height: 847px;
    background: linear-gradient(90deg, var(--spine-edge) 0%, #1c1c1c 6%, var(--ink-black) 40%, #262626 88%, #d0d0d0 100%);
  }
  .spine-rule {
    position: absolute; top: 48px; width: 3px; height: 462px;
    background: linear-gradient(180deg, var(--gold-dark), var(--gold-light) 50%, var(--gold-dark));
  }
  .spine-rule.left { left: 18px; }
  .spine-rule.right { left: 87px; }
  .spine-title {
    position: absolute; left: 26px; top: 52px; height: 456px; width: 60px;
    writing-mode: vertical-rl; transform: rotate(180deg); text-align: center;
    font-size: 50px; line-height: 60px; font-weight: 600; letter-spacing: 1px; white-space: nowrap;
  }
  .spine-author {
    position: absolute; left: 40px; top: 568px; height: 256px; width: 32px;
    writing-mode: vertical-rl; transform: rotate(180deg); text-align: center;
    font-size: 24px; line-height: 32px; font-variant: small-caps; font-weight: 500; white-space: nowrap;
  }

  /* Front cover */
  .front {
    position: absolute; left: 657px; top: 0; width: 543px; height: 847px; overflow: hidden;
  }
  .front-scene {
    position: absolute; inset: 0;
    background: linear-gradient(180deg, var(--sky-blue) 0%, var(--sky-light) 40%, #9a98c0 58%, var(--dusk-purple) 76%, var(--night-purple) 100%);
  }
  .title-panel {
    position: absolute; left: 76px; top: 0; width: 425px; height: 308px;
    background: radial-gradient(ellipse at 50% 30%, #d8232c 0%, var(--deep-red) 55%, #7e0b11 100%);
  }
  .front .title-block {
    left: 76px; top: 66px; width: 425px;
    text-shadow: 1px 1px 0 #d9d9d9, 2px 2px 0 #bdbdbd, 3px 3px 0 #9a9a9a, 4px 5px 6px rgba(0,0,0,.55);
  }
  .front .title-main { font-size: 112px; }
  .front .title-rule { width: 348px; margin-top: 12px; }
  .front .title-sub { font-size: 70px; margin-top: 10px; }
  .subtitle {
    position: absolute; left: 0; top: 318px; width: 543px; text-align: center;
    color: var(--title-red); font-size: 27px; font-weight: 700; font-variant: small-caps;
    text-shadow: 1px 2px 3px rgba(255,255,255,.5);
  }
  .author-plate {
    position: absolute; left: 126px; top: 780px; width: 280px; height: 56px;
    border-radius: 12px 12px 0 0;
    background: rgba(20,14,36,.72);
    font-size: 28px; font-weight: 500; font-variant: small-caps;
    display: flex; align-items: center; justify-content: center;
  }
</style>
</head>
<body>
<main class="cover">

  <section class="back">
    <h2 class="title-block">
      <span class="title-main">IRON</span>
      <span class="title-rule"></span>
      <span class="title-sub">LEDGER</span>
    </h2>
    <p class="author-bio">
      <span class="author-photo" role="img" aria-label="Portrait photograph of the author"></span>
      Lorem ipsum dolor sit amet, consectetur adipiscing elit. In eget nibh eu nulla imperdiet feugiat. Cum sociis natoque penatibus et magnis dis parturient montes, nascetur ridiculus mus. Sed in ante consectetur sem feugiat eleifend ac vel enim. Fusce quis est in nisi pretium facilisis. Etiam adipiscing interdum libero, aliquam aliquet orci cursus quis. Aliquam lobortis lacus quis purus tempor pretium. Aliquam ut placerat dui. Integer dictum risus dui, sit amet consequat nunc blandit ac. Aenean porttitor eros at felis ornare feugiat. Aenean sit amet nulla sem. Proin sem neque, imperdiet aliquet pulvinar et, hendrerit nec augue. Interdum et malesuada fames ac ante ipsum primis in faucibus.
    </p>
    <div class="site-button">WWW.MARCUSHALE.COM</div>
  </section>

  <section class="spine">
    <span class="spine-rule left"></span>
    <span class="spine-rule right"></span>
    <div class="spine-title">IRON LEDGER</div>
    <div class="spine-author">Marcus Hale</div>
  </section>

  <section class="front">
    <div class="front-scene" role="img" aria-label="Photograph of a person with raised arms standing under a wide open sky"></div>
    <div class="title-panel" role="img" aria-label="Red cloud-textured title panel"></div>
    <h1 class="title-block">
      <span class="title-main">IRON</span>
      <span class="title-rule"></span>
      <span class="title-sub">LEDGER</span>
    </h1>
    <p class="subtitle">She Never Leaves the Harbor</p>
    <div class="author-plate">Marcus Hale</div>
  </section>

</main>
</body>
</html>
```